Business Card Design for Marketing Firm

Looking for business card design for higher end marketing firm. Clean but impressionable/trendy. We are a marketing firm that represents manufacturers in the foodservice equipment and supply industry. Our customers are end users such has hotels, restaurants, country clubs, convention centers and casinos as well as distributors of restaurants supplies and equipment, and manufacturers of foodservice equipment and supplies.
Target Market(s)
Hotels, Restaurants, Supply & Equipment Distributors, Foodservice Manufacturers
Industry/Entity Type
Foodservice/Hospitality
Contact Information for Business Card
Name, Title, Contact Number, Email, Website, Social Media, Address
Requirements
Must have
- Clean & Simple but Serious and Impressionable

```html
<!DOCTYPE html>
<html lang="en">
<head>
<meta charset="utf-8">
<title>Northgate Hospitality Reps – Business Card</title>
<link rel="stylesheet" href="https://fonts.googleapis.com/css2?family=Cinzel:wght@400&family=Montserrat:wght@400;700&display=swap">
<style>
  :root {
    --backdrop: #616161;
    --paper: #efeff1;
    --navy: #1b1a70;
    --ink: #1d1d24;
  }
  * { box-sizing: border-box; margin: 0; padding: 0; }
  html, body {
    width: 1200px; height: 1047px; overflow: hidden;
    background: var(--backdrop);
  }
  .stage { position: relative; width: 1200px; height: 1047px; }
  .card {
    position: absolute;
    background: var(--paper);
    border-bottom: 4px solid var(--navy);
    box-shadow: 0 10px 28px rgba(0,0,0,.28);
  }

  /* Contact side (portrait) */
  .card--contact { left: 120px; top: 226px; width: 340px; height: 595px; }
  .brand-block { position: absolute; left: 40px; top: 58px; width: 260px; }
  .brand-name {
    font-family: "Cinzel", serif; font-weight: 400;
    font-size: 25px; line-height: 1.15; letter-spacing: .5px;
    color: var(--navy);
  }
  .brand-dot {
    display: block; width: 14px; height: 14px; border-radius: 50%;
    background: var(--navy); margin-bottom: 14px;
  }
  .brand-rule { height: 1.5px; background: var(--navy); margin-top: 16px; width: 250px; }

  .person { position: absolute; left: 40px; top: 290px; }
  .person-name {
    font-family: "Montserrat", sans-serif; font-weight: 700;
    font-size: 19px; letter-spacing: .5px; color: var(--navy);
  }
  .person-title {
    font-family: "Montserrat", sans-serif; font-weight: 400;
    font-size: 15px; color: var(--ink); margin-top: 2px;
  }
  .icon-row { position: absolute; left: 40px; top: 360px; display: flex; align-items: center; gap: 6px; }
  .icon-row .rule { width: 70px; height: 1.5px; background: var(--navy); }
  .icon-row .rule--short { width: 40px; }
  .icon { width: 24px; height: 24px; }
  .contact-list {
    position: absolute; left: 40px; top: 404px; list-style: none;
    font-family: "Montserrat", sans-serif; font-size: 15px; line-height: 1.45; color: var(--ink);
  }
  .contact-rule { position: absolute; left: 40px; top: 486px; width: 240px; height: 1.5px; background: var(--navy); }
  .address {
    position: absolute; left: 40px; top: 500px; font-style: normal;
    font-family: "Montserrat", sans-serif; font-size: 15px; line-height: 1.4; color: var(--ink);
  }

  /* Brand side (landscape) */
  .card--brand { left: 500px; top: 353px; width: 595px; height: 340px; }
  .front-lockup { position: absolute; left: 60px; right: 60px; top: 96px; text-align: center; }
  .front-dot { display: inline-block; width: 22px; height: 22px; border-radius: 50%; background: var(--navy); margin-bottom: 22px; }
  .front-name {
    font-family: "Cinzel", serif; font-weight: 400;
    font-size: 36px; letter-spacing: 1px; color: var(--navy); line-height: 1.2;
  }
  .front-rule { height: 1.5px; background: var(--navy); width: 360px; margin: 20px auto 0; }
</style>
</head>
<body>
<main class="stage">

  <section class="card card--contact" aria-label="Business card, contact side">
    <div class="brand-block">
      <span class="brand-dot"></span>
      <p class="brand-name">Northgate Hospitality Reps</p>
      <div class="brand-rule"></div>
    </div>

    <div class="person">
      <p class="person-name">DANIEL REYES</p>
      <p class="person-title">Managing Director</p>
    </div>

    <div class="icon-row">
      <span class="rule rule--short"></span>
      <svg class="icon" viewBox="0 0 24 24" aria-label="Phone">
        <rect width="24" height="24" rx="5" fill="var(--navy)"/>
        <path d="M8 6.5c.6-.5 1.3-.4 1.6.2l1 2c.2.5.1 1-.3 1.3l-.8.6c.6 1.4 1.6 2.4 2.9 3l.6-.8c.3-.4.9-.5 1.3-.3l2 1c.6.3.7 1 .2 1.6l-.9.9c-.8.8-2.1.9-3.1.3-2.4-1.3-4.3-3.3-5.5-5.7-.5-1-.4-2.2.4-3z" fill="#fff"/>
      </svg>
      <svg class="icon" viewBox="0 0 24 24" aria-label="Email">
        <rect width="24" height="24" rx="5" fill="var(--navy)"/>
        <rect x="5.5" y="7.5" width="13" height="9" rx="1" fill="none" stroke="#fff" stroke-width="1.5"/>
        <path d="M6 8.2l6 4.5 6-4.5" fill="none" stroke="#fff" stroke-width="1.5"/>
      </svg>
      <svg class="icon" viewBox="0 0 24 24" aria-label="Website">
        <rect width="24" height="24" rx="5" fill="var(--navy)"/>
        <circle cx="12" cy="12" r="6" fill="none" stroke="#fff" stroke-width="1.4"/>
        <ellipse cx="12" cy="12" rx="2.6" ry="6" fill="none" stroke="#fff" stroke-width="1.2"/>
        <path d="M6 12h12" stroke="#fff" stroke-width="1.2"/>
      </svg>
      <span class="rule"></span>
    </div>

    <ul class="contact-list">
      <li>555 014 782</li>
      <li>hello@northgatereps.com</li>
      <li>www.northgatereps.com</li>
    </ul>
    <div class="contact-rule"></div>
    <address class="address">4180 Marina Crest Way<br>Bay Harbor CA 90417</address>
  </section>

  <section class="card card--brand" aria-label="Business card, brand side">
    <div class="front-lockup">
      <span class="front-dot"></span>
      <p class="front-name">Northgate Hospitality Reps</p>
      <div class="front-rule"></div>
    </div>
  </section>

</main>
</body>
</html>
```